Quorva - corporate Business Card

We need a good look and innovative business card for a new start up company based in Los Angeles called "Quorva". We are in a payment business, including payment card, app, and ewallet. We are expert in online payment and Card not present (CNP) transaction.
We need an innovative, modern business card.

Our logo font is Aero Matics

Target Market(s)

Startup - Bank - Online Payment - Card Manufacturing

Industry/Entity Type

Startup

Contact Information for Business Card

phone: 555 014 7396 - Address: 4172 Marlowe blvd, Tessin Park, OR 97299

Requirements
Must have
• Message: innovative, professional, expert, high tech, trust, online payment expert, security
Nice to have
• no comment
Should not have
• no Comment

```html
<!DOCTYPE html>
<html lang="en">
<head>
<meta charset="utf-8">
<title>Quorva – Business Card</title>
<link href="https://fonts.googleapis.com/css2?family=Open+Sans:wght@400;600&display=swap" rel="stylesheet">
<style>
  :root {
    --backdrop: #3a3230;
    --card: #111111;
    --brand-red: #c0202f;
    --text-light: #f2f2f2;
  }
  html, body {
    margin: 0;
    padding: 0;
    width: 1200px;
    height: 844px;
    overflow: hidden;
    background: var(--backdrop);
    font-family: "Open Sans", Arial, sans-serif;
  }
  .canvas {
    position: relative;
    width: 1200px;
    height: 844px;
  }
  .card {
    position: absolute;
    top: 272px;
    width: 520px;
    height: 297px;
    background: var(--card);
    box-shadow: 0 14px 30px rgba(0,0,0,0.45);
    color: var(--text-light);
  }
  .card--front { left: 50px; }
  .card--back  { left: 630px; }

  .brand {
    display: flex;
    align-items: center;
    gap: 14px;
  }
  .brand__dot {
    border-radius: 50%;
    background: var(--brand-red);
    flex: none;
  }
  .brand__name {
    color: var(--brand-red);
    font-weight: 600;
    letter-spacing: 1px;
    line-height: 1;
  }

  /* Front */
  .card--front .brand {
    position: absolute;
    left: 30px;
    top: 38px;
  }
  .card--front .brand__dot { width: 84px; height: 84px; }
  .card--front .brand__name { font-size: 60px; }

  .contact {
    position: absolute;
    right: 30px;
    top: 140px;
    text-align: right;
    font-size: 13px;
    line-height: 22px;
  }
  .contact__row {
    display: flex;
    justify-content: flex-end;
    align-items: center;
    gap: 8px;
  }
  .contact__icon { width: 11px; height: 11px; }

  .person {
    position: absolute;
    left: 30px;
    bottom: 42px;
  }
  .person__name {
    color: var(--brand-red);
    font-weight: 600;
    font-size: 18px;
    line-height: 22px;
  }
  .person__role {
    font-size: 14px;
    line-height: 18px;
  }
  .address {
    position: absolute;
    right: 30px;
    bottom: 30px;
    font-size: 14px;
  }

  /* Back */
  .card--back .brand {
    position: absolute;
    left: 0;
    right: 0;
    top: 80px;
    justify-content: center;
  }
  .card--back .brand__dot { width: 78px; height: 78px; }
  .card--back .brand__name { font-size: 56px; }
  .tagline {
    position: absolute;
    left: 0;
    right: 0;
    top: 184px;
    margin: 0;
    text-align: center;
    font-size: 13px;
    line-height: 18px;
  }
</style>
</head>
<body>
<main class="canvas">

  <section class="card card--front" aria-label="Business card front">
    <div class="brand">
      <span class="brand__dot"></span>
      <span class="brand__name">quorva</span>
    </div>

    <div class="contact">
      <div class="contact__row">
        <span>555 014 7396</span>
        <svg class="contact__icon" viewBox="0 0 12 12" aria-hidden="true">
          <path d="M2.5 1 L4.5 1 L5.2 3.4 L4 4.4 C4.7 6 6 7.3 7.6 8 L8.6 6.8 L11 7.5 L11 9.5 C11 10.3 10.3 11 9.5 11 C5 11 1 7 1 2.5 C1 1.7 1.7 1 2.5 1 Z" fill="var(--brand-red)"/>
        </svg>
      </div>
      <div class="contact__row">
        <span>www.quorva.com</span>
        <svg class="contact__icon" viewBox="0 0 12 12" aria-hidden="true">
          <circle cx="6" cy="6" r="5.5" fill="var(--brand-red)"/>
          <path d="M1 6 H11 M6 0.5 C3.5 3 3.5 9 6 11.5 M6 0.5 C8.5 3 8.5 9 6 11.5" stroke="var(--card)" stroke-width="0.8" fill="none"/>
        </svg>
      </div>
    </div>

    <div class="person">
      <div class="person__name">Daniel Harwick</div>
      <div class="person__role">Managing Director</div>
    </div>

    <div class="address">4172 Marlowe blvd,&nbsp; Tessin Park, OR 97299</div>
  </section>

  <section class="card card--back" aria-label="Business card back">
    <div class="brand">
      <span class="brand__dot"></span>
      <span class="brand__name">quorva</span>
    </div>
    <p class="tagline">
      Innovative | Professional | Expert | High tech | Trust<br>
      Online payment expert | Security
    </p>
  </section>

</main>
</body>
</html>
```